my website is tavorinque.com. (brand name is ta belle vitrine) This is just a template that i have choose for. The content and the pictures are not about my business just the template.
I would like to have 4 pages for now. 1 homepage, which will be an overview for all pages, it is right now in this way. It will directly highlight my story. My website will tell an exclusive story about details which makes the difference and will make people happy with very small things. It will be art related but very stylish as well. I also want to have a event agenda on my homepage where people can see where my next event is. Page 2 my blog, where I will write weekly about mindset, lifestyle and details. Inspiration place for people who are looking for unique and exclusive approaches in life. Page 3 shop, where I will sell my stuff which is handmade and unique, it will be limited edition stuff. Mostly I will make the designs from marbling art, which I am a teacher for. (https://www.vidoranta.com/watch?v=KpwuzRaxTmo) check this video out for more. Page 4 is book page. Here people will be able to book private or group classes for marbling art (check the video). I have already a community of more than 500 people on gath rix, which will be my public as well. I wanna implement the gath rix button on this page as well. to be able to track.

This is about my website. I also need a logo for my brand, which will suit my website and my goals.

I can also give you a reference website, which really like as structure and style;
https://www.brightorvalco.com/products/the-morning-ledger?gclid=Xr4TpLmwq2HsVD9KEBsZTrc-WkPhyQ-uvlEjdRs3NKaOYFCBWMpuTzG8xyCVbhdnLWRqoaNf_2e8ZtpRvHbAwq9FLQ_hqgQ

Logo Text

ta belle vitrine

Coding

Coded - Design and coding required

Number of Pages Required

4 page

Requirements
Must have
• I can also give you a reference website, which really like as structure and style;
• https://www.brightorvalco.com/products/the-morning-ledger?gclid=Xr4TpLmwq2HsVD9KEBsZTrc-WkPhyQ-uvlEjdRs3NKaOYFCBWMpuTzG8xyCVbhdnLWRqoaNf_2e8ZtpRvHbAwq9FLQ_hqgQ

```html
<!DOCTYPE html>
<html lang="en">
<head>
<meta charset="utf-8">
<title>ta belle vitrine</title>
<link href="https://fonts.googleapis.com/css2?family=Roboto+Slab:wght@400;700&family=Open+Sans:wght@400;600&family=Roboto:wght@400;500&display=swap" rel="stylesheet">
<style>
:root{
  --ink:#1f1b1b;
  --text:#555050;
  --muted:#777;
  --white:#fff;
  --btn:#474344;
  --soft:#f2f2f2;
  --line:#e2e2e2;
  --rose:#cdb7b5;
  --rose-light:#e9d6d4;
  --footer:#3a3231;
  --footer-line:#6a6060;
}
*{box-sizing:border-box;margin:0;padding:0}
html,body{width:1200px;height:3041px;overflow:hidden;background:var(--white)}
body{font-family:"Open Sans",sans-serif;color:var(--text);position:relative}
.slab{font-family:"Roboto Slab",serif}
.btn{display:inline-flex;align-items:center;justify-content:center;font-family:"Roboto Slab",serif;font-size:14px;letter-spacing:.5px;text-transform:uppercase;color:var(--white);background:var(--btn);height:53px;width:146px}
.abs{position:absolute}

/* nav */
.site-nav{position:absolute;top:0;left:0;width:1200px;height:85px;background:var(--white);font-family:"Roboto Slab",serif;font-size:18px;color:var(--ink)}
.site-nav a{position:absolute;top:28px;color:var(--ink);text-decoration:none}
.site-nav .active{border-bottom:2px solid var(--ink);padding-bottom:3px}
.brand{position:absolute;left:520px;top:22px;display:flex;align-items:center;gap:10px;font-family:"Roboto Slab",serif;font-size:20px;color:var(--ink)}
.brand-dot{width:26px;height:26px;border-radius:50%;border:1.5px solid var(--ink)}
.nav-icon{position:absolute;top:24px;width:34px;height:34px;border-radius:50%;border:1px solid #ccc;display:flex;align-items:center;justify-content:center}

/* hero */
.hero{position:absolute;top:85px;left:0;width:1200px;height:430px;background:linear-gradient(160deg,#6d6663 0%,#2c2625 35%,#1d1919 60%,#8a7c72 100%);text-align:center;color:var(--white)}
.hero-title{position:absolute;top:106px;width:100%;font-family:"Roboto Slab",serif;font-weight:700;font-size:46px}
.hero-sub{position:absolute;top:172px;left:200px;width:800px;font-family:"Roboto Slab",serif;font-size:25px;line-height:37px}
.hero .btn{position:absolute;top:270px;left:527px;background:transparent;border:1.5px solid var(--white)}
.dots{position:absolute;top:383px;left:577px;display:flex;gap:5px}
.dots span{width:13px;height:13px;border-radius:50%;border:2px solid var(--white)}
.dots span.on{background:var(--white)}

/* about */
.about-photo{position:absolute;top:590px;left:97px;width:503px;height:320px;border:3px solid #e4e4e4;background:linear-gradient(180deg,#d9d2bf 0%,#a8998a 55%,#2a2f5a 100%)}
.about-title{position:absolute;top:606px;left:622px;font-family:"Roboto Slab",serif;font-weight:700;font-size:30px;color:var(--ink)}
.about-text{position:absolute;top:664px;left:622px;width:480px;font-size:15px;line-height:24px;color:var(--muted)}
.about-text p{margin-bottom:12px}
.about .btn{position:absolute;top:835px;left:622px;width:150px}

/* products */
.products{position:absolute;top:977px;left:0;width:1200px;height:892px;background:var(--soft)}
.section-title{position:absolute;width:100%;text-align:center;font-family:"Roboto Slab",serif;font-weight:700;font-size:30px;color:var(--ink)}
.card{position:absolute;width:220px;height:274px;background:var(--white);border:1px solid var(--line);border-radius:6px;overflow:hidden}
.card-img{height:198px}
.card-name{position:absolute;left:16px;top:206px;font-family:"Roboto",sans-serif;font-size:16px;color:#666}
.card-price{position:absolute;left:16px;top:230px;font-family:"Roboto",sans-serif;font-weight:500;font-size:20px;color:var(--ink)}
.cart{position:absolute;right:22px;top:212px;width:38px;height:38px;border-radius:50%;background:var(--btn);display:flex;align-items:center;justify-content:center}
.products .btn{position:absolute;top:766px;left:527px}

/* arrivals */
.arrivals{position:absolute;top:1869px;left:0;width:1200px;height:349px;background:linear-gradient(120deg,#d9c4c3 0%,#e6d5d3 45%,#cbb7bd 75%,#dac9c7 100%);text-align:center}
.arrivals-title{position:absolute;top:76px;width:100%;font-family:"Roboto Slab",serif;font-weight:700;font-size:36px;color:var(--ink)}
.arrivals-text{position:absolute;top:138px;left:140px;width:920px;font-size:22px;line-height:32px;color:var(--ink)}
.arrivals .btn{position:absolute;top:221px;left:527px}

/* events */
.event{position:absolute;top:2355px;width:497px;height:232px;background:var(--white);border:1px solid var(--line);border-radius:6px}
.event-img{position:absolute;top:8px;width:229px;height:216px}
.event-date{position:absolute;top:8px;width:58px;height:72px;background:var(--rose);color:var(--white);font-family:"Roboto Slab",serif;font-size:24px;line-height:28px;text-align:center;padding-top:8px;opacity:.92}
.event-title{position:absolute;top:34px;font-family:"Roboto Slab",serif;font-weight:700;font-size:20px;color:var(--ink)}
.event-text{position:absolute;top:78px;width:232px;font-size:13px;line-height:23px;color:#666}
.event-more{position:absolute;top:180px;font-family:"Roboto Slab",serif;font-size:14px;color:var(--rose)}
.arrow{position:absolute;top:2456px}

/* footer */
.site-footer{position:absolute;top:2690px;left:0;width:1200px;height:351px;background:var(--footer);color:var(--white)}
.foot-head{position:absolute;top:58px;font-family:"Roboto Slab",serif;font-weight:700;font-size:18px}
.foot-about{position:absolute;top:106px;left:100px;width:360px;font-size:13px;line-height:22px}
.foot-links{position:absolute;top:100px;left:572px;font-size:13px;line-height:23px;list-style:none}
.field{position:absolute;left:768px;width:333px;height:33px;border:1px solid #ccc;font-size:11px;padding:8px 10px}
.submit{position:absolute;left:1003px;top:202px;width:98px;height:31px;background:var(--rose-light);color:var(--ink);font-family:"Roboto Slab",serif;font-weight:700;font-size:13px;display:flex;align-items:center;justify-content:center;text-transform:uppercase}
.foot-rule{position:absolute;top:271px;left:100px;width:1001px;height:1px;background:var(--footer-line)}
.copyright{position:absolute;top:300px;left:100px;font-size:12px}
.pay{position:absolute;top:298px;width:36px;height:22px;border-radius:3px}
</style>
</head>
<body>

<header class="site-nav">
  <a class="active" style="left:230px">Home</a>
  <a style="left:363px">Blog</a>
  <div class="brand"><span class="brand-dot"></span>ta belle vitrine</div>
  <a style="left:787px">Shop</a>
  <a style="left:913px">Book</a>
  <div class="nav-icon" style="left:1022px"><svg width="14" height="14" viewBox="0 0 14 14"><circle cx="7" cy="4" r="3" fill="#1f1b1b"/><path d="M1 14c0-4 3-6 6-6s6 2 6 6z" fill="#1f1b1b"/></svg></div>
  <div class="nav-icon" style="left:1066px"><svg width="16" height="14" viewBox="0 0 16 14"><path d="M0 1h3l2 8h8l2-6H4.5" fill="none" stroke="#1f1b1b" stroke-width="1.8"/><circle cx="6" cy="12" r="1.5" fill="#1f1b1b"/><circle cx="12" cy="12" r="1.5" fill="#1f1b1b"/></svg></div>
</header>

<section class="hero" role="img" aria-label="Marbling tray with floating colour on dark size">
  <h1 class="hero-title">ta belle vitrine</h1>
  <p class="hero-sub">We provide an unparalleled selection of the very best quality products, an easy and comfortable shopping experience.</p>
  <span class="btn">Read more</span>
  <div class="dots"><span class="on"></span><span></span><span></span></div>
</section>

<section class="about">
  <div class="about-photo" role="img" aria-label="Two makers at a table of marbled cards"></div>
  <h2 class="about-title">Who We Are ?</h2>
  <div class="about-text">
    <p>Ta belle vitrine is a trendsetting Online Store, offering our first-rate products and exceptional customer service to shoppers from the comfort of their own homes.</p>
    <p>We're a business made up of innovators and forward-thinkers, with the drive and wherewithal to constantly update and improve the online shopping experience.</p>
  </div>
  <span class="btn">Read more</span>
</section>

<section class="products">
  <h2 class="section-title" style="top:72px">Our Products</h2>

  <div class="card" style="left:97px;top:134px"><div class="card-img" role="img" aria-label="Marbled cat collage in a round frame" style="background:radial-gradient(circle,#d7cfc6 40%,#c9a86a 60%,#e8ddd0 75%)"></div><div class="card-name">Lorem Ipsum</div><div class="card-price">$ 40.99</div><div class="cart"><svg width="16" height="14" viewBox="0 0 16 14"><path d="M0 1h3l2 8h8l2-6H4.5" fill="none" stroke="#fff" stroke-width="1.8"/><circle cx="6" cy="12" r="1.5" fill="#fff"/><circle cx="12" cy="12" r="1.5" fill="#fff"/></svg></div></div>
  <div class="card" style="left:359px;top:134px"><div class="card-img" role="img" aria-label="Hanging shell chandelier" style="background:linear-gradient(180deg,#e6e6e6,#cfcfcf 50%,#e9e9e9)"></div><div class="card-name">Lorem Ipsum</div><div class="card-price">$ 40.99</div><div class="cart"><svg width="16" height="14" viewBox="0 0 16 14"><path d="M0 1h3l2 8h8l2-6H4.5" fill="none" stroke="#fff" stroke-width="1.8"/><circle cx="6" cy="12" r="1.5" fill="#fff"/><circle cx="12" cy="12" r="1.5" fill="#fff"/></svg></div></div>
  <div class="card" style="left:618px;top:134px"><div class="card-img" role="img" aria-label="Ochre marbled paper pattern" style="background:linear-gradient(135deg,#d9b890,#c89a6a 50%,#e0c29c)"></div><div class="card-name">Lorem Ipsum</div><div class="card-price">$ 40.99</div><div class="cart"><svg width="16" height="14" viewBox="0 0 16 14"><path d="M0 1h3l2 8h8l2-6H4.5" fill="none" stroke="#fff" stroke-width="1.8"/><circle cx="6" cy="12" r="1.5" fill="#fff"/><circle cx="12" cy="12" r="1.5" fill="#fff"/></svg></div></div>
  <div class="card" style="left:878px;top:134px"><div class="card-img" role="img" aria-label="Purple and green marbled pattern" style="background:linear-gradient(135deg,#7a4a6a,#b48aa6 45%,#4f6a3e)"></div><div class="card-name">Lorem Ipsum</div><div class="card-price">$ 40.99</div><div class="cart"><svg width="16" height="14" viewBox="0 0 16 14"><path d="M0 1h3l2 8h8l2-6H4.5" fill="none" stroke="#fff" stroke-width="1.8"/><circle cx="6" cy="12" r="1.5" fill="#fff"/><circle cx="12" cy="12" r="1.5" fill="#fff"/></svg></div></div>

  <div class="card" style="left:97px;top:452px"><div class="card-img" role="img" aria-label="Green marbling bath with floating flowers" style="background:linear-gradient(135deg,#6f8a2a,#9bb04a 50%,#5f7a22)"></div><div class="card-name">Lorem Ipsum</div><div class="card-price">$ 40.99</div><div class="cart"><svg width="16" height="14" viewBox="0 0 16 14"><path d="M0 1h3l2 8h8l2-6H4.5" fill="none" stroke="#fff" stroke-width="1.8"/><circle cx="6" cy="12" r="1.5" fill="#fff"/><circle cx="12" cy="12" r="1.5" fill="#fff"/></svg></div></div>
  <div class="card" style="left:359px;top:452px"><div class="card-img" role="img" aria-label="Blue marbling with dark leaf shape" style="background:linear-gradient(135deg,#6f9ac8,#a9c6e2 50%,#5a86b8)"></div><div class="card-name">Lorem Ipsum</div><div class="card-price">$ 40.99</div><div class="cart"><svg width="16" height="14" viewBox="0 0 16 14"><path d="M0 1h3l2 8h8l2-6H4.5" fill="none" stroke="#fff" stroke-width="1.8"/><circle cx="6" cy="12" r="1.5" fill="#fff"/><circle cx="12" cy="12" r="1.5" fill="#fff"/></svg></div></div>
  <div class="card" style="left:618px;top:452px"><div class="card-img" role="img" aria-label="Red and green marbled cards" style="background:linear-gradient(135deg,#8a3a2e,#c8c0b2 50%,#3e6a3a)"></div><div class="card-name">Lorem Ipsum</div><div class="card-price">$ 40.99</div><div class="cart"><svg width="16" height="14" viewBox="0 0 16 14"><path d="M0 1h3l2 8h8l2-6H4.5" fill="none" stroke="#fff" stroke-width="1.8"/><circle cx="6" cy="12" r="1.5" fill="#fff"/><circle cx="12" cy="12" r="1.5" fill="#fff"/></svg></div></div>
  <div class="card" style="left:878px;top:452px"><div class="card-img" role="img" aria-label="Kraft greeting card with marbled cat" style="background:linear-gradient(180deg,#22243e,#a6865a 45%,#c49a66)"></div><div class="card-name">Lorem Ipsum</div><div class="card-price">$ 40.99</div><div class="cart"><svg width="16" height="14" viewBox="0 0 16 14"><path d="M0 1h3l2 8h8l2-6H4.5" fill="none" stroke="#fff" stroke-width="1.8"/><circle cx="6" cy="12" r="1.5" fill="#fff"/><circle cx="12" cy="12" r="1.5" fill="#fff"/></svg></div></div>

  <span class="btn">View all</span>
</section>

<section class="arrivals" role="img" aria-label="Soft view of marbling paints and brushes">
  <h2 class="arrivals-title">Our New Arrivals Are Here</h2>
  <p class="arrivals-text">Sed ut perspiciatis unde omnis iste natus error sit voluptatem accusantium doloremque laudantium, totam rem aperiam, eaque ipsa quae.</p>
  <span class="btn">Shop now !</span>
</section>

<section class="events">
  <h2 class="section-title" style="top:2290px">Upcoming Events</h2>
  <svg class="arrow" style="left:44px" width="18" height="30" viewBox="0 0 18 30"><path d="M14 4 4 15l10 11" fill="none" stroke="#333" stroke-width="3"/></svg>
  <svg class="arrow" style="left:1138px" width="18" height="30" viewBox="0 0 18 30"><path d="M4 4l10 11L4 26" fill="none" stroke="#333" stroke-width="3"/></svg>

  <article class="event" style="left:91px">
    <div class="event-img" role="img" aria-label="Brown marbled paper at a workshop" style="left:8px;background:linear-gradient(160deg,#3a3434 0%,#8a5a44 40%,#a8705a 100%)"></div>
    <div class="event-date" style="left:8px">Oct<br>17</div>
    <h3 class="event-title" style="left:255px">Lorem Ipsum</h3>
    <p class="event-text" style="left:255px">Lorem ipsum dolor sit amet, conec tetur adipiscing elit, sed do eiusmod tempor incididunt ut labore et dolore magna aliqua.</p>
    <span class="event-more" style="left:255px">Read More »</span>
  </article>

  <article class="event" style="left:610px">
    <h3 class="event-title" style="left:15px">Lorem Ipsum</h3>
    <p class="event-text" style="left:15px">Lorem ipsum dolor sit amet, conec tetur adipiscing elit, sed do eiusmod tempor incididunt ut labore et dolore magna aliqua.</p>
    <span class="event-more" style="left:15px">Read More »</span>
    <div class="event-img" role="img" aria-label="Pink and green floral marbling" style="left:260px;background:linear-gradient(160deg,#8a3a3a 0%,#5c8a7a 40%,#8ab8b8 100%)"></div>
    <div class="event-date" style="left:431px">Oct<br>25</div>
  </article>
</section>

<footer class="site-footer">
  <h4 class="foot-head" style="left:100px">ABOUT US</h4>
  <p class="foot-about">Ta belle vitrine is a leading Online Store. We provide an unparalleled selection of the very best quality products, an easy and comfortable shopping experience.</p>
  <h4 class="foot-head" style="left:572px">LINKS</h4>
  <ul class="foot-links"><li>Home</li><li>Blog</li><li>Shop</li><li>Book</li></ul>
  <h4 class="foot-head" style="left:768px">SUBSCRIBE TO NEWSLETTER</h4>
  <div class="field" style="top:111px">Name</div>
  <div class="field" style="top:154px">Email</div>
  <div class="submit">Submit</div>
  <div class="foot-rule"></div>
  <p class="copyright">Copyright © ta belle vitrine, 2017. All Rights Reserved.</p>
  <span class="pay" style="left:898px;background:#e8e8e8"></span>
  <span class="pay" style="left:939px;background:#d8d8d8"></span>
  <span class="pay" style="left:980px;background:#e8e8e8"></span>
  <span class="pay" style="left:1021px;background:#6a9ad8"></span>
  <span class="pay" style="left:1062px;background:#e8e8e8"></span>
</footer>

</body>
</html>
```